Freeze Dried Raw Dog Food Label

Create a label for a Freeze Dried Raw dog and cat food line.
There are four flavors (beef, bison, fish and chicken).
4 x 8" Label FRONT AND BACK
Please see website www.tolvarfeeds.com for our other product labels that this will need to stand next to.
Please use this color codes for the different flavors:
Chicken: #d5c55c
Beef: 469b9f
Bison: #275e6d
Fish: #a07980
The only other colors that should be used are Black, White, gray scale, and the shiny metallic gold as seen on our website: www.tolvarfeeds.com
There will have 8 Variations:
Beef for dogs
Beef for Cats
Chicken for dogs
Chicken for cats
Bison for dogs
Bison for cats
Fish for dogs
Fish for cats.
There will be (2) 4X8 inch labels for each variation (a front side and a back side)
The Nutritional Information of the 4 flavors, is as follows:
BEEF
Ingredients
Beef, Beef Kidneys, Beef Hearts, Beef Liver, Whole Egg, Flaxseed, Organic Sweet Potato, Kelp, Organic Carrots, Organic Apples, Organic Blueberries, Cod Liver Oil, Pumpkin Seeds, Organic Spinach, Chicory Root, Organic Cranberries, Ginger, Mixed Tocopherols, Inulin, Dried Enterococcus faecium, Fermentation Product, Dried Lactobacillus acidophilus fermentation product
Calorie Content
Kcal/Cup 182
Guaranteed Analysis
Crude Protein – 38% (min)
Crude Fat – 36% (min)
Crude Fiber – 4% (max)
Moisture – 5% (max)
CHICKEN
Ingredients
Chicken, Chicken Liver, Chicken Hearts, Whole Egg, Flaxseed, Organic Sweet Potato, Kelp, Organic Carrots, Organic Apples, Organic Blueberries, Cod Liver Oil, Pumpkin Seeds, Organic Spinach, Chicory Root, Organic Cranberries, Ginger, Mixed Tocopherols, Inulin, Dried Enterococcus faecium, Fermentation Product, Dried Lactobacillus acidophilus fermentation product.
Calorie Content
Kcal/Cup 185
Guaranteed Analysis
Crude Protein – 45% (min)
Crude Fat – 34% (min)
Crude Fiber – 4% (max)
Moisture – 5% (max)
BISON:
Ingredients
Bison, Bison kidneys, Bison Livers, Whole Egg, Flaxseed, Organic Sweet Potato, Kelp, Organic Carrots, Organic Apples, Organic Blueberries, Cod Liver Oil, Pumpkin Seeds, Organic Spinach, Chicory Root, Organic Cranberries, Ginger, Mixed Tocopherols, Inulin, Dried Enterococcus faecium, Fermentation Product, Dried Lactobacillus acidophilus fermentation product.
Calorie Content
Kcal/Cup 186
Guaranteed Analysis
Crude Protein – 32% (min)
Crude Fat – 38% (min)
Crude Fiber – 5% (max)
Moisture – 5% (max)
FISH
Ingredients
Tuna, Salmon, Pollock, Whole Egg, Flaxseed, Organic Sweet Potato, Kelp, Organic Carrots, Organic Apples, Organic Blueberries, Cod Liver Oil, Pumpkin Seeds, Organic Spinach, Chicory Root, Organic Cranberries, Ginger, Mixed Tocopherols, Inulin, Dried Enterococcus faecium, Fermentation Product, Dried Lactobacillus acidophilus fermentation product.
Calorie Content
Kcal/Cup 455, Kcal/oz 114
Guaranteed Analysis
Crude Protein – 40% (min)
Crude Fat – 37% (min)
Crude Fiber – 4% (max)
Moisture – 5% (max)
THINGS TO ADD
Feeding Guidelines: Insert a QR CODE

```html
<!DOCTYPE html>
<html lang="en">
<head>
<meta charset="utf-8">
<title>Freeze Dried Raw Food – Chicken Formula for Dogs</title>
<link rel="stylesheet" href="https://fonts.googleapis.com/css2?family=Bebas+Neue&display=swap">
<style>
  :root {
    --paper: #ffffff;
    --chicken: #d5c55c;
    --chicken-soft: #e3d895;
    --ink: #3a3a3c;
    --black: #111111;
  }
  html, body {
    margin: 0;
    padding: 0;
    width: 1200px;
    height: 2400px;
    overflow: hidden;
    background: var(--paper);
  }
  .label {
    display: block;
    width: 1200px;
    height: 2400px;
  }
  .label text {
    font-family: "Bebas Neue", "Oswald", sans-serif;
  }
  .ribbon { fill: var(--chicken); }
  .ribbon-text { fill: var(--paper); font-size: 136px; }
  .headline { fill: var(--ink); font-size: 270px; }
  .flavor { fill: var(--chicken); font-size: 122px; }
  .rule { stroke: var(--black); stroke-width: 7; }
  .claims { fill: var(--black); font-size: 48px; }
  .net-weight { fill: var(--black); font-size: 50px; }
</style>
</head>
<body>
<svg class="label" viewBox="0 0 1200 2400" xmlns="http://www.w3.org/2000/svg">
  <defs>
    <radialGradient id="hen-tone" cx="0.5" cy="0.5" r="0.5">
      <stop offset="0" stop-color="#e3d895" stop-opacity="0.55"/>
      <stop offset="0.6" stop-color="#e3d895" stop-opacity="0.3"/>
      <stop offset="1" stop-color="#e3d895" stop-opacity="0"/>
    </radialGradient>
    <radialGradient id="grass-tone" cx="0.5" cy="0.5" r="0.5">
      <stop offset="0" stop-color="#e3d895" stop-opacity="0.45"/>
      <stop offset="0.7" stop-color="#e3d895" stop-opacity="0.2"/>
      <stop offset="1" stop-color="#e3d895" stop-opacity="0"/>
    </radialGradient>
  </defs>

  <g class="illustration" role="img" aria-label="Engraved-style illustration of a hen standing on grass, in pale gold line work">
    <ellipse cx="820" cy="1130" rx="470" ry="600" fill="url(#hen-tone)"/>
    <ellipse cx="650" cy="1640" rx="560" ry="90" fill="url(#grass-tone)"/>
  </g>

  <g class="flag">
    <polygon class="ribbon" points="867,0 1037,0 1037,622 947,597 867,622"/>
    <text class="ribbon-text" transform="translate(1003,555) rotate(-90)" textLength="440" lengthAdjust="spacingAndGlyphs">FOR DOGS</text>
  </g>

  <g class="product-name">
    <text class="headline" x="145" y="1005" textLength="605" lengthAdjust="spacingAndGlyphs">FREEZE</text>
    <text class="headline" x="145" y="1265" textLength="487" lengthAdjust="spacingAndGlyphs">DRIED</text>
    <text class="headline" x="145" y="1523" textLength="923" lengthAdjust="spacingAndGlyphs">RAW FOOD</text>
  </g>

  <text class="flavor" x="258" y="1920" textLength="760" lengthAdjust="spacingAndGlyphs">CHICKEN FORMULA</text>

  <g class="claims-block">
    <line class="rule" x1="138" y1="2038" x2="1064" y2="2038"/>
    <text class="claims" x="393" y="2110" textLength="392" lengthAdjust="spacing">NATURAL PRODUCT,</text>
    <text class="claims" x="182" y="2172" textLength="836" lengthAdjust="spacing">FREE OF METALS, PESTICIDES, MICROBES</text>
    <line class="rule" x1="138" y1="2216" x2="1064" y2="2216"/>
  </g>

  <text class="net-weight" x="479" y="2318" textLength="243" lengthAdjust="spacing">NET.WT 2LB</text>
</svg>
</body>
</html>
```